Law Firm Advertising Design Needed

Law Office of Dalmer K Quoss provides legal services to businesses and individuals who have been or are being injured. Our main practice area is personal injury (car accidents, wrongful death, premises liability), but we are looking for an ad that highlights a lesser known area of our practice - insurance company bad faith and breach of contract.

This ad will be placed in 8 1/2" x 11" format in a local neighborhood directory. It will also be placed in a smaller format (to be determined) in the local newspaper of a region of Arizona that has recently lost a considerable number of homes and people to wildfire.

We want to convey through the ad that our firm is available to help if their insurance company is not paying a legitimate claim or not paying enough for their claim.

Because of the tragic nature of the events in Velmont, we would like to avoid images of fire or anything resembling fire. However, the ad should capture the attention of individuals who are struggling through an insurance claim with all the stacks of paperwork and frustrated with unresponsive adjusters and unreasonably low offers.

The design should convey a feeling of safety, security and being taken care of.

Information that must be included in the ad are: the firm name (Law Office of Dalmer K Quoss), address (47390 N 18th Street, Ste 506, Phoenix, AZ 85044), the phone number (602-514-7730) and the fact that we have mobile offices available to assist in your area.

An example of text that has been used in the past is here:
"If your own insurance company is refusing to pay what you are owed on a claim, call the Law Office of Dalmer K Quoss. We fight for you by examining the reasons your insurance carrier is denying or making an insufficient offer on the claim; updating and correcting claim documentation; making a new demand and filing a lawsuit if necessary. Whether it's a simple misunderstanding or something more complicated, we can help!

Here are a few of the kinds of claims we handle:
- Hit and Run or Uninsured driver claims
- Fire, flood and property loss
- Life insurance benefits
- Health insurance claims
- Catastrophic losses
- Business insurance
- Wrongful Death Benefits

Our attorneys are available to help you cut through the nonsense. Call to make an appointment for a free consultation with an attorney today. "

An example of a previous ad for car accident services is attached for reference.
Updates

Hi Everyone,

The main lawyer involved in the decision making process has been giving me some feedback in general on the designs that I thought I would pass along.  He does not want the name of the law firm to be the first thing you notice when you look at the ad. Try to keep that small and possibly to the bottom of the ad. The phone number should be rather large, but the address should be rather small (we are required by the Lawyers' Guild to include our address, but we don't want our location to limit the location of our clients because our mobile offices can travel to them).  He would prefer that the logo either not be included or be not a significant part of the ad.

                                   

Thanks!  I will continue providing individual feedback to ads received. 

Target Market(s)

Low to middle income residents of the State of Arizona with little or no college education

Industry/Entity Type

Insurance

```html
<!DOCTYPE html>
<html lang="en">
<head>
<meta charset="utf-8">
<title>We Fight For You – Law Office of Dalmer K Quoss</title>
<link href="https://fonts.googleapis.com/css2?family=Cinzel:wght@600;700&family=Arimo:wght@400;700&display=swap" rel="stylesheet">
<style>
  :root {
    --page-bg: #e6e6e6;
    --teal-deep: #154f66;
    --teal-header: #1a5b75;
    --teal-mid: #14506a;
    --teal-band: #1b5f7c;
    --teal-footer: #106690;
    --white: #ffffff;
    --wall: #7d8790;
    --crowd-dark: #3f3b40;
    --crowd-warm: #8a5a4e;
    --floor: #9a9a9a;
    --shirt: #a8c4da;
    --skin: #d6b8a4;
    --shadow-blue: #2c3b52;
  }
  * { box-sizing: border-box; margin: 0; padding: 0; }
  html, body { width: 1200px; height: 1000px; overflow: hidden; background: var(--page-bg); }
  .flyer {
    position: absolute; left: 259px; top: 59px; width: 682px; height: 882px;
    background: var(--teal-mid); color: var(--white);
    font-family: "Arimo", Arial, sans-serif;
    box-shadow: 0 0 24px rgba(0,0,0,.25);
  }
  .headline-band {
    position: absolute; left: 0; top: 0; width: 100%; height: 92px;
    background: linear-gradient(to bottom, #1d6783, var(--teal-header));
    display: flex; align-items: center; justify-content: center;
  }
  .headline {
    font-family: "Cinzel", "Times New Roman", serif; font-weight: 700;
    font-size: 61px; letter-spacing: 1px; line-height: 1;
  }
  .crowd-photo {
    position: absolute; left: 0; top: 92px; width: 100%; height: 237px;
    background: linear-gradient(to bottom,
      #41657a 0%, var(--wall) 40%, #6d6f74 50%,
      var(--crowd-dark) 60%, var(--crowd-warm) 68%, #4b5670 80%,
      var(--floor) 92%, #8c8c8c 100%);
  }
  .intro {
    position: absolute; left: 13px; top: 101px; width: 656px;
    font-size: 15px; line-height: 16.4px; text-align: justify;
    text-shadow: 0 1px 2px rgba(0,0,0,.55);
  }
  .services {
    position: absolute; left: 0; top: 329px; width: 100%; height: 152px;
    background: linear-gradient(to bottom, var(--teal-deep), var(--teal-mid));
    border-top: 2px solid #2b7896;
  }
  .services-lead { position: absolute; left: 13px; top: 11px; width: 662px; font-size: 15px; line-height: 20px; }
  .claim-list {
    position: absolute; top: 55px; list-style: none;
    font-size: 13.4px; line-height: 18px; letter-spacing: .7px;
  }
  .claim-list.left { left: 58px; }
  .claim-list.right { left: 379px; }
  .phone-photo {
    position: absolute; left: 0; top: 481px; width: 100%; height: 247px;
    background:
      radial-gradient(ellipse 38% 42% at 48% 48%, var(--skin) 0%, rgba(214,184,164,.6) 55%, rgba(214,184,164,0) 100%),
      linear-gradient(to bottom, #c9dbe8 0%, var(--shirt) 45%, #6f86a0 80%, var(--shadow-blue) 100%);
  }
  .firm-band {
    position: absolute; left: 0; top: 728px; width: 100%; height: 64px;
    background: linear-gradient(to bottom, #1f6a88, var(--teal-band));
    border-top: 2px solid #3a88a6;
  }
  .firm-name {
    position: absolute; left: 20px; top: 19px;
    font-family: "Cinzel", "Times New Roman", serif; font-weight: 600;
    font-size: 23px; letter-spacing: 1px; white-space: nowrap;
  }
  .contact { position: absolute; left: 0; top: 792px; width: 100%; height: 90px; background: var(--teal-footer); }
  .contact p { position: absolute; left: 16px; font-size: 15px; letter-spacing: .4px; white-space: nowrap; }
  .contact .address { top: 8px; font-size: 14px; }
  .contact .phone { top: 28px; font-size: 21px; font-weight: 700; }
  .contact .mobile { top: 60px; }
  .brand-mark {
    position: absolute; left: 516px; top: 700px; width: 124px; height: 124px;
    background: var(--white); display: flex; align-items: center; justify-content: center;
    text-align: center;
    font-family: "Cinzel", "Times New Roman", serif; font-weight: 600;
    font-size: 26px; line-height: 30px; color: var(--teal-deep);
  }
</style>
</head>
<body>
  <article class="flyer">
    <header class="headline-band">
      <h1 class="headline">WE FIGHT FOR YOU</h1>
    </header>

    <div class="crowd-photo" role="img" aria-label="Photo of a long line of people waiting against a grey wall"></div>
    <p class="intro">If your own insurance company is refusing to pay what you are owed on a claim, call the Law Office of Dalmer K Quoss. We fight for you by examining the reasons your insurance carrier is denying or making an insufficient offer on the claim; updating and correcting claim documentation; making a new demand and filing a lawsuit if necessary. Whether it's a simple misunderstanding or something more complicated, WE CAN HELP!</p>

    <section class="services">
      <p class="services-lead">Our attorneys are available to help you cut through the nonsense. Call to make an appointment for a free consultation with an attorney today.</p>
      <ul class="claim-list left">
        <li>- Hit and Run or Uninsured driver claims</li>
        <li>- Fire, flood and property loss</li>
        <li>- Life insurance benefits</li>
        <li>- Health insurance claims</li>
      </ul>
      <ul class="claim-list right">
        <li>- Catastrophic losses</li>
        <li>- Business insurance</li>
        <li>- Wrongful Death Benefits</li>
        <li>- and more</li>
      </ul>
    </section>

    <div class="phone-photo" role="img" aria-label="Photo of hands holding a smartphone and dialing"></div>

    <div class="firm-band">
      <h2 class="firm-name">LAW OFFICE OF DALMER K. QUOSS</h2>
    </div>

    <footer class="contact">
      <p class="address">address : 47390 N 18th Street, Ste 506, Phoenix, AZ 85044</p>
      <p class="phone">phone : 602-514-7730</p>
      <p class="mobile">We have mobile offices available to assist in your area. CALL US NOW!</p>
    </footer>

    <div class="brand-mark">Quoss<br>Law</div>
  </article>
</body>
</html>
```